Modern card design needed for building development company

We are looking for a sharp modern new look for our business cards.
We are a New Zealand based company called TKR Ventures NZ LTD that specialises in subdividing large sections, housing and commercial buildings.
We have attached a photo of the current logo and would like to see it improved somehow as it looks a bit dated.
We are open to any colours.

Target Market(s)

Investors, Property buyers

Industry/Entity Type

Investment

Contact Information for Business Card

TKR VENTURES NZ LTD
www.tkrventuresnz.co.nz

Damon Whitcombe
Phone +64 21 938 104
Email dpwhitcombe@korumail.co.nz

Font styles to use
Serif
Sans Serif

Colors
0792cd
33a6d7
85cae6
6b449b
886aae
f04a50
ec1f27
f37122
f68d4d

Requirements
Must have
• Please try and make the logo more modern or if you have a similar one we would like to see it.

```html
<!DOCTYPE html>
<html lang="en">
<head>
<meta charset="utf-8">
<title>TKR Ventures NZ LTD — Business Card</title>
<link href="https://fonts.googleapis.com/css2?family=Montserrat:wght@600;700&family=Work+Sans:wght@300;400&display=swap" rel="stylesheet">
<style>
  :root {
    --backdrop: #2b2b2d;
    --card-dark: #1d1d1f;
    --card-light: #ffffff;
    --brand-red: #8e1b2a;
    --silver: #b9b9bc;
    --ink: #3a3a3a;
    --rule: #2e2e2e;
  }
  * { box-sizing: border-box; margin: 0; padding: 0; }
  html, body { width: 1200px; height: 900px; overflow: hidden; }
  body {
    background: var(--backdrop);
    font-family: "Work Sans", Arial, sans-serif;
    position: relative;
  }
  .card {
    position: absolute;
    left: 290px;
    width: 620px;
    height: 354px;
  }
  .card--back {
    top: 70px;
    background: var(--card-dark);
    display: flex;
    align-items: center;
    justify-content: center;
  }
  .card--front {
    top: 476px;
    background: var(--card-light);
  }
  .brand {
    display: flex;
    align-items: center;
    gap: 10px;
    font-family: "Montserrat", Arial, sans-serif;
    font-weight: 600;
    letter-spacing: 0.12em;
    white-space: nowrap;
  }
  .brand__square { width: 14px; height: 14px; flex: none; }
  .card--back .brand { color: var(--silver); font-size: 19px; }
  .card--back .brand__square { background: var(--silver); }
  .card--front .brand {
    position: absolute;
    right: 50px;
    top: 52px;
    color: var(--brand-red);
    font-size: 14px;
  }
  .card--front .brand__square { background: var(--brand-red); width: 13px; height: 13px; }
  .holder {
    position: absolute;
    left: 56px;
    top: 100px;
  }
  .holder__name {
    font-family: "Montserrat", Arial, sans-serif;
    font-weight: 700;
    font-size: 22px;
    line-height: 28px;
    color: var(--brand-red);
    letter-spacing: 0.02em;
    text-transform: uppercase;
    white-space: nowrap;
  }
  .holder__role {
    font-size: 15px;
    font-weight: 400;
    color: var(--ink);
    margin-top: 2px;
  }
  .card__rule {
    position: absolute;
    left: 56px;
    right: 50px;
    top: 182px;
    height: 1.5px;
    background: var(--rule);
  }
  .contacts {
    position: absolute;
    left: 56px;
    top: 200px;
    list-style: none;
  }
  .contacts li {
    display: flex;
    align-items: center;
    gap: 14px;
    font-size: 16px;
    font-weight: 400;
    color: var(--ink);
    line-height: 25px;
    white-space: nowrap;
  }
  .contacts svg { width: 12px; height: 12px; flex: none; }
  .address {
    position: absolute;
    right: 50px;
    bottom: 42px;
    text-align: right;
    font-style: normal;
    font-size: 17px;
    font-weight: 300;
    color: var(--ink);
    line-height: 26px;
    white-space: nowrap;
  }
</style>
</head>
<body>

  <section class="card card--back" aria-label="Card back">
    <div class="brand"><span class="brand__square"></span>TKR VENTURES NZ LTD</div>
  </section>

  <section class="card card--front" aria-label="Card front">
    <div class="brand"><span class="brand__square"></span>TKR VENTURES NZ LTD</div>

    <div class="holder">
      <h1 class="holder__name">Damon Whitcombe</h1>
      <p class="holder__role">Director</p>
    </div>

    <div class="card__rule"></div>

    <ul class="contacts">
      <li>
        <svg viewBox="0 0 12 12" aria-hidden="true"><path d="M2.5 1h2l1 3-1.4 1a6 6 0 0 0 2.9 2.9l1-1.4 3 1v2a1 1 0 0 1-1 1A9 9 0 0 1 1.5 2a1 1 0 0 1 1-1z" fill="var(--brand-red)"/></svg>
        +64 21 938 104
      </li>
      <li>
        <svg viewBox="0 0 12 12" aria-hidden="true"><rect x="1" y="2.5" width="10" height="7" fill="none" stroke="var(--brand-red)" stroke-width="1.2"/><path d="M1 2.5l5 4 5-4" fill="none" stroke="var(--brand-red)" stroke-width="1.2"/></svg>
        dpwhitcombe@korumail.co.nz
      </li>
      <li>
        <svg viewBox="0 0 12 12" aria-hidden="true"><circle cx="6" cy="6" r="5" fill="none" stroke="var(--brand-red)" stroke-width="1.1"/><ellipse cx="6" cy="6" rx="2.2" ry="5" fill="none" stroke="var(--brand-red)" stroke-width="1"/><path d="M1 6h10" stroke="var(--brand-red)" stroke-width="1"/></svg>
        www.tkrventuresnz.co.nz
      </li>
    </ul>

    <address class="address">
      PO BOX 48215 Northcote<br>
      Auckland New Zealand
    </address>
  </section>

</body>
</html>
```